Corvane Holdings , new business card design

investment firm with corporate clients . need double sided business card , vertical and horizontal options ,logo must be clear. prefer pantone colors only and sharp design. website also www.corvane.ae

Khalid Bin Tarrafi
Managing Director
Tel. +971 4 387 2940
Mobile +971 50 518 2403
khalid@corvane.ae
Q-Span Plaza, officw 18-B07, Warqa Gardens, Dubai

Contact Information for Business Card

Khalid Bin Tarrafi
Managing Director

Font styles to use
Serif

Colors

Designer to choose colors to be used in the design.

```html
<!DOCTYPE html>
<html lang="en">
<head>
<meta charset="utf-8">
<title>Corvane Holdings — Business Card</title>
<link href="https://fonts.googleapis.com/css2?family=Lato:wght@300;400&display=swap" rel="stylesheet">
<style>
  :root {
    --bg: #e9e9e7;
    --card: #f7f7f8;
    --brand-blue: #43709a;
    --ink: #1f1f22;
    --ink-soft: #3a3a3e;
    --rule: #4a4a4e;
  }
  * { box-sizing: border-box; margin: 0; padding: 0; }
  html, body {
    width: 1200px; height: 1200px; overflow: hidden;
    background: var(--bg);
    font-family: "Lato", Arial, sans-serif;
    color: var(--ink);
  }
  .canvas {
    position: relative; width: 1200px; height: 1200px;
  }
  .card {
    position: absolute; left: 150px;
    width: 900px; height: 514px;
    background: var(--card);
    box-shadow: 0 2px 8px rgba(0,0,0,0.12);
    overflow: hidden;
  }
  .card--front { top: 60px; }
  .card--back { top: 626px; }

  .front-sweep { position: absolute; inset: 0; width: 100%; height: 100%; }

  .wordmark {
    position: absolute;
    font-weight: 300;
    color: var(--ink);
    letter-spacing: 0.28em;
    text-transform: uppercase;
    white-space: nowrap;
  }
  .card--front .wordmark {
    right: 70px; top: 235px;
    font-size: 34px;
  }

  .rule {
    position: absolute; left: 56px; right: 56px;
    height: 1.5px; background: var(--rule);
  }
  .rule--top { top: 104px; }
  .rule--bottom { top: 350px; }

  .identity { position: absolute; left: 64px; top: 128px; }
  .identity__name { font-size: 36px; font-weight: 400; color: var(--ink); }
  .identity__title { font-size: 25px; font-weight: 300; color: var(--ink-soft); margin-top: 4px; }

  .card--back .wordmark {
    right: 60px; top: 142px;
    font-size: 26px;
  }

  .contact {
    position: absolute; left: 430px; top: 222px;
    display: grid; grid-template-columns: 96px 22px auto;
    row-gap: 6px;
    font-size: 24px; font-weight: 400; color: var(--ink-soft);
  }

  .location {
    position: absolute; left: 430px; top: 368px;
    font-size: 23px; font-weight: 400; color: var(--ink-soft);
    line-height: 1.35;
  }
  .location__web { margin-bottom: 8px; color: var(--ink); }
</style>
</head>
<body>
<main class="canvas">

  <section class="card card--front" aria-label="Card front">
    <svg class="front-sweep" viewBox="0 0 900 514" preserveAspectRatio="none" aria-hidden="true">
      <path d="M0 0 H580 C380 40 200 250 140 514 H0 Z" fill="var(--brand-blue)"/>
    </svg>
    <div class="wordmark">Corvane Holdings</div>
  </section>

  <section class="card card--back" aria-label="Card back">
    <div class="rule rule--top"></div>

    <div class="identity">
      <div class="identity__name">Khalid Bin Tarrafi</div>
      <div class="identity__title">Managing Director</div>
    </div>

    <div class="wordmark">Corvane Holdings</div>

    <div class="contact">
      <span>Tel</span><span>:</span><span>+971 4 387 2940</span>
      <span>Mobile</span><span>:</span><span>+971 50 518 2403</span>
      <span>Email</span><span>:</span><span>khalid@corvane.ae</span>
    </div>

    <div class="rule rule--bottom"></div>

    <div class="location">
      <div class="location__web">www.corvane.ae</div>
      <div>Q-Span Plaza, officw 18-B07,</div>
      <div>Warqa Gardens, Dubai</div>
    </div>
  </section>

</main>
</body>
</html>
```